Blue Heron Journeys

We are a predominantly online travel agency with high-end (first/business class) clients. I'm looking to either have our existing logo revamped or a new logo created with business card layout. I prefer to work with existing logo if possible so it remains familiar with existing clientele. I have uploaded a yellow business card layout showing icons on one side of the card. I would like to keep my existing colours, not yellow. could the company name/tag line go over the icons?
Industry/Entity Type
Business
Contact Information for Business Card
Lucinda Fairley
Director
(I.A.T.A. 07715463)
(Corvano Pty. Ltd) ABN 61 574 203 918
512/18 Kendrick Lane
Wattle Reach | NSW 2577 | Australia
www.blueheronjourneys.com.au
m: + 61 (0) 417 588 130
t: + 61 (0) 2 9416 2058
e: lucinda@blueheronjourneys.com.au

```html
<!DOCTYPE html>
<html lang="en">
<head>
<meta charset="utf-8">
<title>Blue Heron Journeys – Business Card</title>
<link rel="stylesheet" href="https://fonts.googleapis.com/css2?family=Cormorant+Garamond:wght@500&family=Work+Sans:wght@400&display=swap">
<style>
  :root {
    --backdrop: #e4e4e4;
    --card: #ffffff;
    --peach: #f9cd98;
    --peach-text: #f5b979;
    --ink: #3e3e3e;
  }
  * { margin: 0; padding: 0; box-sizing: border-box; }
  html, body { width: 1200px; height: 900px; overflow: hidden; background: var(--backdrop); }
  .canvas { position: relative; width: 1200px; height: 900px; }
  .card {
    position: absolute; left: 250px; width: 700px; height: 400px;
    background: var(--card);
    box-shadow: 0 2px 10px rgba(0,0,0,0.18);
  }
  .card--back { top: 35px; padding: 14px; }
  .card--front { top: 465px; }
  .travel-pattern { width: 100%; height: 100%; background: var(--peach); }

  .brand { position: absolute; right: 60px; top: 66px; width: 330px; text-align: center; }
  .brand__name {
    font-family: "Cormorant Garamond", serif; font-weight: 500;
    font-size: 38px; color: var(--peach-text); line-height: 1;
  }

  .person { position: absolute; left: 70px; top: 140px; }
  .person__name {
    font-family: "Cormorant Garamond", serif; font-weight: 500;
    font-size: 28px; color: var(--peach-text); margin-bottom: 6px;
  }
  .person__meta { font-family: "Work Sans", sans-serif; font-size: 16px; color: var(--ink); line-height: 1.45; }

  .divider { position: absolute; left: 70px; right: 60px; top: 252px; height: 1.5px; background: var(--peach); }

  .contacts {
    position: absolute; left: 60px; top: 272px; list-style: none;
    font-family: "Work Sans", sans-serif; font-size: 16px; color: var(--ink);
  }
  .contacts li { display: flex; align-items: center; gap: 12px; height: 25px; }
  .contacts svg { width: 14px; height: 14px; flex: none; }

  .office {
    position: absolute; right: 60px; top: 272px; text-align: right; font-style: normal;
    font-family: "Work Sans", sans-serif; font-size: 16px; color: var(--ink); line-height: 1.5;
  }
  .office__company { color: var(--peach-text); letter-spacing: 2px; text-transform: uppercase; }
</style>
</head>
<body>
<div class="canvas">
  <section class="card card--back">
    <div class="travel-pattern" role="img" aria-label="Repeating pattern of white line icons of vehicles: cars, trucks, trains, planes, boats, rockets, balloons and helicopters on peach"></div>
  </section>

  <section class="card card--front">
    <div class="brand">
      <div class="brand__name">Blue Heron Journeys</div>
    </div>

    <div class="person">
      <div class="person__name">Lucinda Fairley</div>
      <div class="person__meta">Director (I.A.T.A. 07715463)<br>ABN 61 574 203 918</div>
    </div>

    <div class="divider"></div>

    <ul class="contacts">
      <li>
        <svg viewBox="0 0 14 14" aria-hidden="true"><rect x="3.5" y="0.8" width="7" height="12.4" rx="1.2" fill="none" stroke="#f9cd98" stroke-width="1.2"/><line x1="6" y1="11" x2="8" y2="11" stroke="#f9cd98" stroke-width="1.2"/></svg>
        + 61 (0) 417 588 130
      </li>
      <li>
        <svg viewBox="0 0 14 14" aria-hidden="true"><path d="M3 1.5l2.2 2.6-1.3 1.5c.8 1.8 2.3 3.3 4.1 4.1l1.5-1.3 2.6 2.2-1.4 2C6.5 12.4 1.6 7.5 1.4 3z" fill="#f9cd98"/></svg>
        + 61 (0) 2 9416 2058
      </li>
      <li>
        <svg viewBox="0 0 14 14" aria-hidden="true"><rect x="1" y="3" width="12" height="8.5" fill="#f9cd98"/><path d="M1 3l6 5 6-5" fill="none" stroke="#fff" stroke-width="1"/></svg>
        lucinda@blueheronjourneys.com.au
      </li>
      <li>
        <svg viewBox="0 0 14 14" aria-hidden="true"><circle cx="7" cy="7" r="6" fill="#f9cd98"/><path d="M1 7h12M7 1c-2.5 3-2.5 9 0 12M7 1c2.5 3 2.5 9 0 12" fill="none" stroke="#fff" stroke-width="0.9"/></svg>
        www.blueheronjourneys.com.au
      </li>
    </ul>

    <address class="office">
      <div class="office__company">Corvano Pty. Ltd</div>
      512/18 Kendrick Lane<br>
      Wattle Reach | NSW 2577<br>
      Australia
    </address>
  </section>
</div>
</body>
</html>
```